Freight broker online presence/customer portal track shipping

I sleek design showing what we do, broker freight. What we specialize in, chemicals and any freight where domestic or international. We want a home page, a customer portal button on front page that lets clients check on status of their freight (integrate with our transportation management system. Contact page,
COMPANIES THAT HAVE PALLETS TO MOVE.
https://www.tallowmerelogistics.com/
https://www.quivendale.com/
https://www.rkpellow.com/
3 page

```html
<!DOCTYPE html>
<html lang="en">
<head>
<meta charset="utf-8">
<title>Freight Broker — Home</title>
<link rel="stylesheet" href="https://fonts.googleapis.com/css2?family=Poppins:wght@400;500;600;700;800&family=Hind:wght@400;500;600&family=IBM+Plex+Sans:wght@500;600&display=swap">
<style>
:root{
  --blue:#2b62a8;
  --blue-dark:#245593;
  --red:#ec2a37;
  --teal:#2bab8f;
  --ink:#1d1d1f;
  --soft:#f5f0f1;
  --footer:#231f20;
  --white:#ffffff;
  --muted:#cfd3d8;
}
*{margin:0;padding:0;box-sizing:border-box}
html,body{width:1200px;height:3762px;overflow:hidden}
body{position:relative;font-family:"Hind",sans-serif;color:var(--ink);background:var(--soft)}
.abs{position:absolute}
.btn{position:absolute;display:flex;align-items:center;justify-content:center;background:var(--red);color:var(--white);font-family:"Poppins",sans-serif;font-weight:600;font-size:13px;letter-spacing:.3px;border-radius:6px;text-decoration:none}

/* hero */
.hero{position:absolute;left:0;top:0;width:1200px;height:674px;background:linear-gradient(180deg,#7b8aa0 0%,#b9a57f 30%,#e3a24a 45%,#6d5a3d 58%,#4a4a3c 75%,#7e7059 100%)}
.nav-logo{position:absolute;left:50px;top:20px;display:flex;align-items:center;gap:14px}
.nav-logo .dot{width:46px;height:46px;border-radius:50%;background:var(--blue)}
.nav-logo span{font-family:"Poppins",sans-serif;font-weight:600;font-size:26px;color:var(--white)}
.nav{position:absolute;top:26px;left:469px;display:flex;gap:0;font-family:"IBM Plex Sans",sans-serif;font-weight:500;font-size:15px;color:var(--white)}
.nav a{color:var(--white);text-decoration:none;height:32px;display:flex;align-items:center;position:absolute;white-space:nowrap}
.nav a.active{background:var(--red);padding:0 12px}
.portal{position:absolute;left:1009px;top:23px;width:168px;height:37px;border:2px solid var(--white);border-radius:8px;color:var(--white);font-family:"IBM Plex Sans",sans-serif;font-weight:600;font-size:14px;display:flex;align-items:center;justify-content:center;text-decoration:none}
.caption{position:absolute;left:793px;top:277px;width:407px;height:231px;background:rgba(40,40,40,.72);padding:33px 0 0 42px;color:var(--white)}
.caption h1{font-family:"Poppins",sans-serif;font-weight:600;font-size:32px;line-height:1;letter-spacing:-.3px}
.caption p{font-size:16px;line-height:20px;margin-top:14px;width:320px}
.caption .btn{left:45px;top:149px;width:128px;height:44px;font-size:15px}
.dots{position:absolute;left:562px;top:628px;display:flex;gap:12px;align-items:center}
.dots i{width:6px;height:6px;border-radius:50%;background:var(--white);display:block}
.dots i.on{width:11px;height:11px;border:2px solid var(--red);background:var(--white)}

/* welcome */
.welcome{position:absolute;left:0;top:674px;width:1200px;height:494px;background:var(--blue);color:var(--white)}
.welcome .kicker{position:absolute;left:131px;top:60px;font-family:"Poppins",sans-serif;font-weight:600;font-size:19px}
.welcome h2{position:absolute;left:131px;top:90px;font-family:"Poppins",sans-serif;font-weight:700;font-size:35px}
.welcome .rule{position:absolute;left:131px;top:152px;width:77px;height:2px;background:var(--white)}
.welcome p{position:absolute;left:131px;top:186px;width:336px;font-size:16px;line-height:22.4px}
.welcome .btn{left:133px;top:394px;width:108px;height:37px;font-size:13px}
.welcome .photo{position:absolute;left:534px;top:57px;width:535px;height:381px;background:linear-gradient(180deg,#3f5f93 0%,#8ea5c9 45%,#c7d2e2 62%,#6d7f9c 100%)}

/* logistics */
.port{position:absolute;left:0;top:1168px;width:1200px;height:371px;background:linear-gradient(100deg,#4c4a52 0%,#8b6a58 40%,#c8874a 70%,#f1a23b 90%,#b77a3a 100%)}
.card{position:absolute;left:131px;top:1342px;width:938px;height:557px;background:var(--white);box-shadow:0 2px 6px rgba(0,0,0,.06);text-align:center}
.card h2{position:absolute;left:0;right:0;top:45px;font-family:"Poppins",sans-serif;font-weight:500;font-size:27px}
.card .lead{position:absolute;left:0;right:0;top:105px;font-size:13.5px;line-height:19.5px}
.svc{position:absolute;top:190px;width:235px;height:243px}
.svc+.svc{border-left:1px solid #dcdcdc}
.svc svg{position:absolute;left:50%;transform:translateX(-50%);top:22px}
.svc h3{position:absolute;left:0;right:0;top:128px;font-family:"Poppins",sans-serif;font-weight:500;font-size:15px}
.svc p{position:absolute;left:36px;right:36px;top:160px;font-size:12.5px;line-height:17.5px}
.card .btn{left:387px;top:476px;width:162px;height:35px}

/* different */
.diff-title{position:absolute;left:0;right:0;top:1964px;text-align:center;font-family:"Poppins",sans-serif;font-weight:500;font-size:27px}
.diff-sub{position:absolute;left:0;right:0;top:2017px;text-align:center;font-size:13.5px}
.diff-photo{position:absolute;left:477px;top:2091px;width:250px;height:355px;border-radius:20px;background:linear-gradient(180deg,#dfe7f1 0%,#b6c9dd 40%,#c9584a 55%,#3a6fa4 68%,#6e95b8 100%)}
.feat{position:absolute;width:330px;height:80px}
.feat .ic{position:absolute;left:0;top:0;width:77px;height:77px;border-radius:18px;background:var(--blue);display:flex;align-items:center;justify-content:center}
.feat h4{position:absolute;left:99px;top:10px;font-family:"Poppins",sans-serif;font-weight:500;font-size:14px}
.feat p{position:absolute;left:99px;top:40px;width:232px;font-size:12.5px;line-height:17.5px}

/* blog */
.blog{position:absolute;left:0;top:2508px;width:1200px;height:552px;background:var(--blue);color:var(--white)}
.blog h2{position:absolute;left:0;right:0;top:44px;text-align:center;font-family:"Poppins",sans-serif;font-weight:500;font-size:27px}
.blog .rule{position:absolute;left:575px;top:101px;width:50px;height:2px;background:var(--white)}
.post{position:absolute;top:161px;width:292px;height:312px;border:2px solid var(--white)}
.post h3{position:absolute;left:27px;top:26px;width:245px;font-family:"Poppins",sans-serif;font-weight:500;font-size:19px;line-height:27px}
.post p{position:absolute;left:29px;top:142px;width:210px;font-size:13.5px;line-height:17.5px}
.post .btn{left:31px;top:294px;width:97px;height:31px;font-size:11.5px}

/* help */
.help{position:absolute;left:0;top:3060px;width:1200px;height:356px;background:var(--teal);color:var(--white);text-align:center}
.help h2{position:absolute;left:0;right:0;top:64px;font-family:"Poppins",sans-serif;font-weight:800;font-size:32px;letter-spacing:-.5px}
.help p{position:absolute;left:250px;right:250px;top:134px;font-size:19.5px;line-height:29px}
.help .btn{left:515px;top:257px;width:138px;height:41px;font-size:13px}

/* footer */
.footer{position:absolute;left:0;top:3416px;width:1200px;height:346px;background:var(--footer);color:var(--white)}
.f-logo{position:absolute;left:134px;top:88px;display:flex;align-items:center;gap:14px}
.f-logo .dot{width:72px;height:72px;border-radius:50%;background:var(--blue)}
.f-logo span{font-family:"Poppins",sans-serif;font-weight:600;font-size:25px}
.f-head{position:absolute;top:44px;font-family:"IBM Plex Sans",sans-serif;font-weight:600;font-size:13px;letter-spacing:.3px}
.f-menu{position:absolute;left:482px;top:80px;list-style:none;font-family:"IBM Plex Sans",sans-serif;font-size:12px;line-height:19.8px}
.f-item{position:absolute;display:flex;gap:10px;align-items:flex-start;font-size:12px;line-height:15px;font-family:"IBM Plex Sans",sans-serif}
.f-item .c{flex:none;width:23px;height:23px;border-radius:50%;background:var(--white);display:flex;align-items:center;justify-content:center}
.f-rule{position:absolute;left:131px;top:260px;width:938px;height:1px;background:#3a3536}
.copy{position:absolute;left:0;right:0;top:303px;text-align:center;font-size:10px;font-family:"IBM Plex Sans",sans-serif}
</style>
</head>
<body>

<header class="hero" role="img" aria-label="Photo of a white semi truck with trailer driving on a highway at sunset">
  <div class="nav-logo"><div class="dot"></div><span>Freight Broker</span></div>
  <nav class="nav">
    <a class="active" style="left:0">HOME</a>
    <a style="left:87px">ABOUT US</a>
    <a style="left:198px">SERVICES</a>
    <a style="left:308px">CAREERS</a>
    <a style="left:413px">CONTACT US</a>
  </nav>
  <a class="portal">CUSTOMER PORTAL</a>
  <div class="caption">
    <h1>BROKER FREIGHT</h1>
    <p>Lorem Ipsum is simply dummy text of the printing and typesetting.</p>
    <a class="btn">READ MORE</a>
  </div>
  <div class="dots"><i></i><i></i><i class="on"></i><i></i><i></i></div>
</header>

<section class="welcome">
  <div class="kicker">Welcome to</div>
  <h2>Freight Broker</h2>
  <div class="rule"></div>
  <p>There are many variations of passages of Lorem Ipsum available, but the majority have suffered alteration in some form, by injected humour, or randomised words which don't look even slightly believable. If you are going to use a passage of Lorem Ipsum, you need to be sure there isn't anything embarrassing hidden in the middle of text.</p>
  <a class="btn">READ MORE</a>
  <div class="photo" role="img" aria-label="Photo of a passenger jet taking off over a runway under a cloudy blue sky"></div>
</section>

<div class="port" role="img" aria-label="Photo of a container port with cranes and stacked containers at sunset"></div>

<section class="card">
  <h2>Global Integrated Logistics</h2>
  <p class="lead">There are many variations of passages of Lorem Ipsum available, but the majority have suffered<br>alteration in some form, by injected humour, or randomised words which don't look.</p>

  <div class="svc" style="left:0">
    <svg width="96" height="66" viewBox="0 0 96 66" fill="none" stroke="#2b62a8" stroke-width="2.4" stroke-linejoin="round"><path d="M6 30 L14 30 L22 38 L78 38 C88 38 92 32 86 28 C80 24 60 26 50 26 L36 8 L28 8 L36 26 L22 26 L14 20 L8 20 Z"/><path d="M44 38 L32 62 L40 62 L60 38"/><circle cx="52" cy="32" r="1.5"/><circle cx="60" cy="32" r="1.5"/><circle cx="68" cy="32" r="1.5"/></svg>
    <h3>Air Freight</h3>
    <p>There are many variations of passages of Lorem Ipsum available, but the majority have suffered alter.</p>
  </div>
  <div class="svc" style="left:234px">
    <svg width="80" height="60" viewBox="0 0 80 60" fill="none" stroke="#2b62a8" stroke-width="2.4" stroke-linejoin="round"><path d="M4 36 L76 36 L70 54 L10 54 Z"/><rect x="8" y="20" width="52" height="16"/><path d="M20 20v16M32 20v16M44 20v16"/><rect x="62" y="8" width="12" height="28"/><path d="M66 4v4"/></svg>
    <h3>Ocean Freight</h3>
    <p>There are many variations of passages of Lorem Ipsum available, but the majority have suffered alter.</p>
  </div>
  <div class="svc" style="left:469px">
    <svg width="110" height="60" viewBox="0 0 110 60" fill="none" stroke="#2b62a8" stroke-width="2.4" stroke-linejoin="round"><rect x="4" y="8" width="74" height="34"/><path d="M78 18 L96 18 L106 30 L106 44 L78 44"/><path d="M84 22 L94 22 L100 30 L84 30 Z"/><circle cx="18" cy="50" r="6"/><circle cx="32" cy="50" r="6"/><circle cx="74" cy="50" r="6"/><circle cx="92" cy="50" r="6"/></svg>
    <h3>Road Freight</h3>
    <p>There are many variations of passages of Lorem Ipsum available, but the majority have suffered alter.</p>
  </div>
  <div class="svc" style="left:703px">
    <svg width="60" height="66" viewBox="0 0 60 66" fill="none" stroke="#2b62a8" stroke-width="2.4" stroke-linejoin="round"><path d="M6 4 L36 4 L46 14 L46 62 L6 62 Z"/><path d="M36 4v10h10"/><path d="M14 24h24M14 32h24M14 40h16M14 48h12"/><path d="M54 26 L36 50 L32 56 L38 52 L56 28 Z"/></svg>
    <h3>Contract Logistics</h3>
    <p>There are many variations of passages of Lorem Ipsum available, but the majority have suffered alter.</p>
  </div>
  <a class="btn">VIEW ALL SERVICES</a>
</section>

<h2 class="diff-title">What makes us different?</h2>
<p class="diff-sub">There are many variations of passages of Lorem Ipsum available lorem ipsum</p>
<div class="diff-photo" role="img" aria-label="Photo of a container cargo ship loaded with colourful containers at sea"></div>

<div class="feat" style="left:133px;top:2104px"><div class="ic"><svg width="40" height="40" viewBox="0 0 40 40" fill="none" stroke="#fff" stroke-width="2.5"><circle cx="20" cy="20" r="16"/><path d="M4 20h32M20 4c-6 5-6 27 0 32M20 4c6 5 6 27 0 32"/></svg></div><h4>Global Network</h4><p>There are many variations of passages of Lorem Ipsum available</p></div>
<div class="feat" style="left:133px;top:2229px"><div class="ic"><svg width="44" height="34" viewBox="0 0 44 34" fill="#fff"><rect x="2" y="4" width="26" height="20" rx="2"/><path d="M30 10h7l5 7v7H30z"/><circle cx="10" cy="28" r="4"/><circle cx="34" cy="28" r="4"/></svg></div><h4>Specialist Logistics Solutions</h4><p>There are many variations of passages of Lorem Ipsum available</p></div>
<div class="feat" style="left:133px;top:2356px"><div class="ic"><svg width="40" height="40" viewBox="0 0 40 40" fill="none" stroke="#fff" stroke-width="3" stroke-linejoin="round"><path d="M20 6 L30 22 L10 22 Z"/><path d="M8 30 L32 30"/><path d="M28 26l4 4-4 4M12 34l-4-4 4-4"/></svg></div><h4>Sustainability</h4><p>There are many variations of passages of Lorem Ipsum available</p></div>

<div class="feat" style="left:756px;top:2104px"><div class="ic"><svg width="40" height="40" viewBox="0 0 40 40" fill="none" stroke="#fff" stroke-width="2.5"><circle cx="20" cy="20" r="16"/><path d="M14 11c-2 1-3 3-2 6 2 6 7 11 13 13 3 1 5 0 6-2l-4-4-3 2c-3-1-6-4-7-7l2-3z" fill="#fff"/></svg></div><h4>Support</h4><p>There are many variations of passages of Lorem Ipsum available</p></div>
<div class="feat" style="left:756px;top:2229px"><div class="ic"><svg width="40" height="40" viewBox="0 0 40 40" fill="none" stroke="#fff" stroke-width="3.5" stroke-linecap="round" stroke-linejoin="round"><path d="M9 21 L17 29 L32 12"/></svg></div><h4>Social Responsibility</h4><p>There are many variations of passages of Lorem Ipsum available</p></div>
<div class="feat" style="left:756px;top:2356px"><div class="ic"><svg width="40" height="40" viewBox="0 0 40 40" fill="#fff"><rect x="6" y="14" width="28" height="20" rx="3"/><path d="M15 14v-4a2 2 0 0 1 2-2h6a2 2 0 0 1 2 2v4h-3v-3h-4v3z"/></svg></div><h4>Professionalism</h4><p>There are many variations of passages of Lorem Ipsum available</p></div>

<section class="blog">
  <h2>Latest Blog</h2>
  <div class="rule"></div>
  <article class="post" style="left:134px"><h3>Lorem Ipsum is simply dummy text of the printing and typesetting industry</h3><p>Sed ut perspiciatis unde omnis iste natus error sit voluptatem accusantium doloremque laudantium, totam rem aperiam, eaque ipsa quae ab illo inventore veritatis et quasi architecto beatae vitae dicta s</p><a class="btn">READ MORE</a></article>
  <article class="post" style="left:457px"><h3>Lorem Ipsum is simply dummy text of the printing and typesetting industry</h3><p>Sed ut perspiciatis unde omnis iste natus error sit voluptatem accusantium doloremque laudantium, totam rem aperiam, eaque ipsa quae ab illo inventore veritatis et quasi architecto beatae vitae dicta s</p><a class="btn">READ MORE</a></article>
  <article class="post" style="left:778px"><h3>Lorem Ipsum is simply dummy text of the printing and typesetting industry</h3><p>Sed ut perspiciatis unde omnis iste natus error sit voluptatem accusantium doloremque laudantium, totam rem aperiam, eaque ipsa quae ab illo inventore veritatis et quasi architecto beatae vitae dicta s</p><a class="btn">READ MORE</a></article>
</section>

<section class="help">
  <h2>HOW CAN WE HELP YOU?</h2>
  <p>At vero eos et accusamus et iusto odio dignissimos ducimus qui blanditiis praesentium voluptatum deleniti atque corrupti quos dolores et quas molestias excepturi sint occaecati cupiditate non provident,</p>
  <a class="btn">CONTACT US</a>
</section>

<footer class="footer">
  <div class="f-logo"><div class="dot"></div><span>Freight Broker</span></div>

  <div class="f-head" style="left:482px">MENU</div>
  <ul class="f-menu"><li>HOME</li><li>ABOUT US</li><li>SERVICES</li><li>CAREERS</li><li>CONTACT US</li></ul>

  <div class="f-head" style="left:673px">CONTACT US</div>
  <div class="f-item" style="left:671px;top:84px"><span class="c"><svg width="10" height="12" viewBox="0 0 10 12"><path d="M5 0a4 4 0 0 0-4 4c0 3 4 8 4 8s4-5 4-8a4 4 0 0 0-4-4z" fill="#231f20"/><circle cx="5" cy="4" r="1.4" fill="#fff"/></svg></span><span>4870 Marlow Yard Road<br>Dunhaven, CA 90000</span></div>
  <div class="f-item" style="left:671px;top:135px"><span class="c"><svg width="11" height="11" viewBox="0 0 12 12"><path d="M2 1c-1 1-1 3 1 6s5 5 7 4l1-2-2-2-2 1C6 7 5 6 4 5l1-2-2-2z" fill="#231f20"/></svg></span><span>Call Us<br>555.014.2290</span></div>
  <div class="f-item" style="left:671px;top:186px"><span class="c"><svg width="12" height="9" viewBox="0 0 12 9"><rect x="0" y="0" width="12" height="9" rx="1" fill="#231f20"/><path d="M0 1l6 4 6-4" stroke="#fff" fill="none"/></svg></span><span>E mail Us<br>hello@freightbroker-desk.com</span></div>

  <div class="f-head" style="left:963px">FOLLOW US</div>
  <div class="f-item" style="left:963px;top:84px"><span class="c"></span><span>Like us on<br>CHATTERBOARD</span></div>
  <div class="f-item" style="left:963px;top:135px"><span class="c"></span><span>Follow us on<br>PINGLINE</span></div>
  <div class="f-item" style="left:963px;top:186px"><span class="c"></span><span>Follow us on<br>LINKWORKS</span></div>

  <div class="f-rule"></div>
  <div class="copy">Copyright © 2021 All Rights Reserved</div>
</footer>

</body>
</html>
```